Climbing Gear Company Stationary Design

We need some new stationary to standardise our business.
We require:

Business Card
A4 Letterhead
With complements slip

Our business is a Distributor and retailer of rock climbing equipment throughout Australia.
We need to the stationary (business card in particular) to reflect this.

Target Market(s)

customers, other retail outlets, overseas manufacturers.

Industry/Entity Type

Business

Requirements
Must have
• company logo
website url- www.ridgetopgearworks.com.au
email - mark@ridgetopgearworks.com
Business Address: Unit 3, 14-16 Marlowe Street, Kestrel Point, NCR, 2371
Phone: 0438 627 194
my Name (on Business card) - Gordon Pellimore
use of Blue colour in our logo

```html
<!DOCTYPE html>
<html lang="en">
<head>
<meta charset="utf-8">
<title>Ridgetop Gearworks – Business Card</title>
<link rel="stylesheet" href="https://fonts.googleapis.com/css2?family=Exo+2:wght@400;600;800&family=Open+Sans:wght@300;400&display=swap">
<style>
  :root {
    --brand-blue: #2d4c96;
    --card-white: #ffffff;
    --ink: #2b2b2b;
    --ink-soft: #444444;
    --rule: #c9cfdc;
    --backdrop: #e9ecf0;
  }
  * { box-sizing: border-box; margin: 0; padding: 0; }
  html, body { width: 1200px; height: 960px; overflow: hidden; }
  body {
    background: var(--backdrop);
    display: flex;
    flex-direction: column;
    align-items: center;
    justify-content: center;
    gap: 44px;
    font-family: "Exo 2", sans-serif;
  }
  .card {
    position: relative;
    width: 680px;
    height: 416px;
    box-shadow: 0 6px 18px rgba(0,0,0,0.15);
    overflow: hidden;
  }

  /* Front */
  .card--front { background: var(--brand-blue); color: var(--card-white); }
  .edge-tab {
    position: absolute;
    width: 26px;
    height: 92px;
    background: var(--card-white);
  }
  .card--front .edge-tab--left { left: 0; top: 186px; }
  .card--front .edge-tab--right { right: 0; top: 112px; }
  .front-brand {
    position: absolute;
    left: 60px; right: 60px;
    top: 150px;
    text-align: center;
  }
  .wordmark {
    font-family: "Exo 2", sans-serif;
    font-weight: 800;
    text-transform: uppercase;
    letter-spacing: 0.5px;
    white-space: nowrap;
  }
  .front-brand .wordmark { font-size: 48px; color: var(--card-white); }
  .tagline {
    margin-top: 10px;
    font-family: "Open Sans", sans-serif;
    font-weight: 300;
    font-size: 21px;
    letter-spacing: 4px;
    white-space: nowrap;
  }

  /* Back */
  .card--back { background: var(--card-white); color: var(--ink); }
  .back-brand {
    position: absolute;
    left: 0; right: 0;
    top: 34px;
    text-align: center;
  }
  .back-brand .wordmark { font-size: 38px; color: var(--brand-blue); }
  .holder-name {
    position: absolute;
    left: 0; right: 0;
    top: 150px;
    text-align: center;
    font-size: 30px;
    font-weight: 400;
    letter-spacing: 1.5px;
    color: var(--brand-blue);
  }
  .bar-pair {
    position: absolute;
    top: 150px;
    display: flex;
    gap: 10px;
    height: 50px;
  }
  .bar-pair span { display: block; background: var(--brand-blue); height: 100%; }
  .bar-pair .bar-thick { width: 26px; }
  .bar-pair .bar-thin { width: 8px; }
  .bar-pair--left { left: 0; top: 110px; }
  .bar-pair--right { right: 0; top: 160px; }
  .contact-list {
    position: absolute;
    left: 40px;
    top: 258px;
    list-style: none;
    font-size: 19px;
    line-height: 28px;
  }
  .contact-list li { display: flex; align-items: center; gap: 14px; white-space: nowrap; }
  .contact-list svg { width: 14px; height: 14px; fill: var(--brand-blue); }
  .divider {
    position: absolute;
    left: 418px;
    top: 258px;
    width: 1px;
    height: 84px;
    background: var(--rule);
  }
  .address {
    position: absolute;
    left: 440px;
    top: 282px;
    font-size: 18px;
    line-height: 24px;
    font-style: normal;
    color: var(--ink-soft);
    white-space: nowrap;
  }
</style>
</head>
<body>

  <section class="card card--front" aria-label="Business card front">
    <span class="edge-tab edge-tab--left"></span>
    <span class="edge-tab edge-tab--right"></span>
    <div class="front-brand">
      <div class="wordmark">Ridgetop Gearworks</div>
      <p class="tagline">THE KIT • THE CRAG • THE ADVENTURE</p>
    </div>
  </section>

  <section class="card card--back" aria-label="Business card back">
    <div class="back-brand"><div class="wordmark">Ridgetop Gearworks</div></div>
    <h1 class="holder-name">Gordon Pellimore</h1>
    <div class="bar-pair bar-pair--left"><span class="bar-thick"></span><span class="bar-thin"></span></div>
    <div class="bar-pair bar-pair--right"><span class="bar-thin"></span><span class="bar-thick"></span></div>

    <ul class="contact-list">
      <li>
        <svg viewBox="0 0 16 16" aria-hidden="true"><path d="M3.5 1.5l2.5 2.6-1.4 1.9c.9 2 2.4 3.5 4.4 4.4l1.9-1.4 2.6 2.5-1.5 2.5C6.4 13.7 2.3 9.6 1 3z"/></svg>
        <span>0438 627 194</span>
      </li>
      <li>
        <svg viewBox="0 0 16 16" aria-hidden="true"><path d="M1 3h14v10H1z M1 3l7 6 7-6" stroke="#fff" stroke-width="1.2"/></svg>
        <span>mark@ridgetopgearworks.com</span>
      </li>
      <li>
        <svg viewBox="0 0 16 16" aria-hidden="true"><circle cx="8" cy="8" r="7"/></svg>
        <span>www.ridgetopgearworks.com.au</span>
      </li>
    </ul>

    <span class="divider"></span>

    <address class="address">
      Unit 3, 14-16 Marlowe Street,<br>
      Kestrel Point, NCR, 2371
    </address>
  </section>

</body>
</html>
```